Tech business card design

We need an amazing business card design for our new business 'Pexla' a marketing tech startup based in Sydney, Australia. We provide an online marketplace for businesses to search and buy advertising media, connect with service providers and learn more about marketing. We wish to communicate 'cool tech', reliability and professionalism and design based around our logo.

Target Market(s)

Business Owners

Contact Information for Business Card

Name
Position
Email Address
Website
Phone Number

Font styles to use
Other font styles liked:
• Avenir & Avenir Next

Colors

Designer to choose colors to be used in the design.

```html
<!DOCTYPE html>
<html lang="en">
<head>
<meta charset="utf-8">
<title>Pexla Business Card</title>
<link rel="stylesheet" href="https://fonts.googleapis.com/css2?family=Nunito+Sans:wght@400;600;700;800;900&display=swap">
<style>
  :root {
    --stage: #1c1b1a;
    --navy: #161b4a;
    --navy-back: #171c4c;
    --grey-band: #75777b;
    --white: #ffffff;
    --lavender: #9c9fbb;
    --web-grey: #8a8db0;
  }
  * { box-sizing: border-box; margin: 0; padding: 0; }
  html, body {
    width: 1200px; height: 900px; overflow: hidden;
    background: var(--stage);
    font-family: "Nunito Sans", "Avenir Next", Arial, sans-serif;
  }
  .canvas { position: relative; width: 1200px; height: 900px; }

  .card {
    position: absolute;
    width: 520px; height: 300px;
    border-radius: 26px;
    overflow: hidden;
    box-shadow: 0 18px 40px rgba(0,0,0,.55);
  }
  .card-front { left: 80px; top: 120px; background: var(--white); }
  .card-back  { left: 600px; top: 470px; background: var(--navy-back); }

  .front-shapes { position: absolute; inset: 0; }

  .wordmark-front {
    position: absolute; left: 150px; top: 12px;
    font-weight: 900; font-size: 96px; letter-spacing: -2px;
    color: var(--navy); line-height: 1;
  }

  .person { position: absolute; left: 30px; top: 188px; color: var(--white); }
  .person-name { font-weight: 800; font-size: 19px; letter-spacing: .5px; }
  .person-role { font-weight: 700; font-size: 14px; margin-left: 10px; }

  .address {
    position: absolute; left: 40px; top: 250px;
    color: var(--white); font-size: 14px; line-height: 1.25;
  }

  .contacts {
    position: absolute; left: 355px; top: 140px;
    list-style: none; color: var(--white); font-size: 14px; line-height: 1.4;
  }
  .contacts li { display: flex; align-items: center; gap: 5px; }
  .contacts svg { width: 12px; height: 12px; flex: none; }

  .wordmark-back {
    position: absolute; left: 0; right: 0; top: 58px;
    text-align: center;
    font-weight: 900; font-size: 150px; letter-spacing: -3px;
    color: var(--lavender); line-height: 1;
  }
  .web-back {
    position: absolute; left: 0; right: 0; top: 222px;
    text-align: center; font-size: 15px; letter-spacing: 5px;
    color: var(--web-grey);
  }
</style>
</head>
<body>
<main class="canvas">

  <section class="card card-front" aria-label="Front of business card">
    <svg class="front-shapes" viewBox="0 0 520 300" width="520" height="300" aria-hidden="true">
      <polygon class="band-grey" points="0,200 520,80 520,116 0,236" fill="#75777b"/>
      <polygon class="band-navy" points="0,236 520,116 520,300 0,300" fill="#161b4a"/>
      <g class="avatar-icon">
        <circle cx="265" cy="156" r="32" fill="#161b4a" stroke="#ffffff" stroke-width="3"/>
        <circle cx="265" cy="146" r="9" fill="#ffffff"/>
        <path d="M249 172 q0 -14 16 -14 q16 0 16 14 z" fill="#ffffff"/>
      </g>
    </svg>

    <div class="wordmark-front">Pexla</div>

    <div class="person">
      <div class="person-name">JOHN SMITH</div>
      <div class="person-role">Position</div>
    </div>

    <address class="address" style="font-style:normal">
      Street Name, City Name<br>Zipcode:012345
    </address>

    <ul class="contacts">
      <li>
        <svg viewBox="0 0 12 12"><path d="M2.5 1 L4.5 1 L5.2 3.5 L4 4.5 Q5 7 7.5 8 L8.5 6.8 L11 7.5 L11 9.5 Q10.5 11 9 11 Q1 10 1 3 Q1 1.5 2.5 1 Z" fill="#fff"/></svg>
        012-345-6789
      </li>
      <li>
        <svg viewBox="0 0 12 12"><rect x="1" y="2.5" width="10" height="7" fill="none" stroke="#fff" stroke-width="1.2"/><path d="M1 2.5 L6 6.5 L11 2.5" fill="none" stroke="#fff" stroke-width="1.2"/></svg>
        info@pexla.com
      </li>
      <li>
        <svg viewBox="0 0 12 12"><circle cx="6" cy="6" r="5" fill="none" stroke="#fff" stroke-width="1"/><ellipse cx="6" cy="6" rx="2.2" ry="5" fill="none" stroke="#fff" stroke-width="1"/><line x1="1" y1="6" x2="11" y2="6" stroke="#fff" stroke-width="1"/></svg>
        www.pexla.com
      </li>
    </ul>
  </section>

  <section class="card card-back" aria-label="Back of business card">
    <div class="wordmark-back">Pexla</div>
    <div class="web-back">www.pexla.com</div>
  </section>

</main>
</body>
</html>
```